New Business Card Design Project

Need a design that will create an impact / strong impression towards our clients for our business. We are in the lighting business and we do lighting retrofits for large commercial to industrial clientele.

Target Market(s)

Lighting Industry

Industry/Entity Type

Business

Font styles to use
Other font styles liked:
• we would like to use the font on our logo, not sure what it is though..

Requirements
Must have
• Our logo.
Nice to have
• We are open to suggestions that have to do with lighting.

```html
<!DOCTYPE html>
<html lang="en">
<head>
<meta charset="utf-8">
<title>Brightline Retrofit – Business Card</title>
<link href="https://fonts.googleapis.com/css2?family=Roboto:wght@400;500;700&family=Roboto+Condensed:wght@500;700&display=swap" rel="stylesheet">
<style>
  :root {
    --bg: #5a4838;
    --card-light: #f2f2f1;
    --forest: #0f3510;
    --green: #1b7a36;
    --green-light: #62bb56;
    --text-grey: #4a4a4a;
    --white: #ffffff;
    --faint: #e2e4e1;
  }
  * { margin: 0; padding: 0; box-sizing: border-box; }
  html, body { width: 1200px; height: 960px; overflow: hidden; }
  body { background: var(--bg); position: relative; font-family: "Roboto", Arial, sans-serif; }

  .card { position: absolute; width: 600px; height: 343px; box-shadow: 2px 3px 4px rgba(0,0,0,.35); overflow: hidden; }
  .card--front { left: 314px; top: 113px; background: var(--card-light); }
  .card--back { left: 311px; top: 472px; background: var(--forest); }

  .front-glow {
    position: absolute; right: 0; bottom: 0; width: 430px; height: 270px;
    background: linear-gradient(160deg, rgba(242,242,241,0) 25%, var(--faint) 100%);
  }

  .brand { position: absolute; display: flex; align-items: center; gap: 12px;
    font-family: "Roboto", Arial, sans-serif; font-weight: 700; letter-spacing: 1px; }
  .brand__mark { width: 16px; height: 16px; }
  .card--front .brand { left: 41px; top: 48px; font-size: 40px; color: var(--forest); }
  .card--front .brand__mark { background: var(--green); }
  .card--back .brand { left: 50%; top: 128px; transform: translateX(-50%); font-size: 44px; color: var(--white); white-space: nowrap; }
  .card--back .brand__mark { background: var(--green-light); }

  .address { position: absolute; left: 41px; top: 167px; font-size: 14.5px; line-height: 19px; color: var(--text-grey); }
  .contacts { position: absolute; left: 41px; top: 214px; list-style: none; font-size: 14.5px; color: var(--text-grey); }
  .contacts li { display: flex; align-items: center; gap: 9px; height: 19px; }
  .contacts svg { width: 13px; height: 13px; fill: var(--forest); flex: none; }

  .person { position: absolute; right: 40px; top: 214px; text-align: right; font-family: "Roboto Condensed", Arial, sans-serif; }
  .person__name { font-size: 23px; font-weight: 700; color: var(--forest); }
  .person__role { font-size: 15px; font-weight: 500; color: var(--green); margin-top: 2px; }

  .website { position: absolute; left: 0; right: 0; top: 283px; text-align: center; color: var(--white); font-size: 14px; letter-spacing: 2.6px; }
</style>
</head>
<body>
  <section class="card card--front">
    <div class="front-glow"></div>
    <div class="brand"><span class="brand__mark"></span>Brightline Retrofit</div>
    <p class="address">214 Birchwood Avenue<br>Juneau, Alaska 99801</p>
    <ul class="contacts">
      <li><svg viewBox="0 0 16 16"><path d="M3 1l3 3-2 2c1 2 3 4 5 5l2-2 3 3-2 3C7 15 1 9 1 3z"/></svg>555 210 4471</li>
      <li><svg viewBox="0 0 16 16"><path d="M4 0h8v16H4zM5.5 2v10h5V2z"/></svg>555 318 2096</li>
      <li><svg viewBox="0 0 16 16"><path d="M4 1h8v4H4zM1 6h14v6H1zM4 10h8v5H4z"/></svg>555 742 6630</li>
      <li><svg viewBox="0 0 16 16"><path d="M1 3h14v10H1zM2 4l6 5 6-5z" fill-rule="evenodd"/></svg>daniel@brightline.co</li>
      <li><svg viewBox="0 0 16 16"><circle cx="8" cy="8" r="7"/></svg>www.brightline.co</li>
    </ul>
    <div class="person">
      <div class="person__name">DANIEL REYES</div>
      <div class="person__role">CEO/FOUNDER</div>
    </div>
  </section>

  <section class="card card--back">
    <div class="brand"><span class="brand__mark"></span>Brightline Retrofit</div>
    <p class="website">www.brightlineretrofit.com</p>
  </section>
</body>
</html>
```